Wall Backdrop - Fern Hollow Roastery -

See the attached logo and wall dimensions. The dimensions are in "inches" We are looking for the backdrop that customers will see walking up to the front of the Roastery. For design we are located in the pacific northwest along the coastal hwy 101 and in the heart of the Mossgrove State Preserve. The Roastery will be located in the Fern Hollow Gaming Hall. Web site www.fernhollowgaminghall.example . We want the back drop to be inviting an can encompass the beautiful nature in the area or a warm, friendly coffee shop.
Updates

The RED X's on the mural wall need to be cut out. No art in the red X areas.

Target Market(s)

50+ in Age, coffee drinkers

Industry/Entity Type

Entertainment

Requirements
Must have
• The Roastery Logo but background doesn't need to match the logo colors
Nice to have
• Something that tells the eyes to have a cup of coffee

```html
<!DOCTYPE html>
<html lang="en">
<head>
<meta charset="utf-8">
<title>Fern Hollow Roastery – Wall Backdrop</title>
<link rel="stylesheet" href="https://fonts.googleapis.com/css2?family=Federo&display=swap">
<style>
  :root {
    --page-bg: #e6e6e6;
    --bark-dark: #3a1f14;
    --bark: #7a3a22;
    --bark-warm: #9c4f2e;
    --moss: #4f7a2c;
    --fern: #6f9a3a;
    --canopy: #8fae5a;
    --path: #8a5a42;
    --cutout: #ffffff;
    --ink-light: #ffffff;
  }
  * { box-sizing: border-box; margin: 0; padding: 0; }
  html, body {
    width: 1200px;
    height: 720px;
    overflow: hidden;
    background: var(--page-bg);
  }
  .backdrop-wall {
    position: absolute;
    left: 42px;
    top: 149px;
    width: 1118px;
    height: 422px;
    overflow: hidden;
    box-shadow: 0 3px 8px rgba(0,0,0,0.45);
  }
  .forest-scene {
    position: absolute;
    inset: 0;
    background:
      linear-gradient(180deg, rgba(143,174,90,0.35) 0%, rgba(0,0,0,0) 40%, rgba(79,122,44,0.75) 80%, var(--moss) 100%),
      linear-gradient(90deg,
        var(--bark-dark) 0%, var(--bark) 6%, var(--bark-warm) 12%, var(--bark) 16%,
        var(--fern) 20%, var(--moss) 26%, var(--bark-dark) 30%,
        var(--bark) 38%, var(--bark-warm) 43%, var(--bark-dark) 48%,
        var(--moss) 51%, var(--bark) 55%, var(--bark-warm) 58%, var(--canopy) 62%,
        var(--fern) 68%, var(--bark-dark) 74%, var(--bark) 80%, var(--bark-warm) 85%,
        var(--moss) 92%, var(--bark) 97%, var(--bark-dark) 100%);
  }
  .cutout {
    position: absolute;
    background: var(--cutout);
  }
  .cutout--left { left: 83px; top: 106px; width: 315px; height: 304px; }
  .cutout--center { left: 558px; top: 172px; width: 260px; height: 129px; }
  .brand-mark {
    position: absolute;
    left: 842px;
    top: 16px;
    width: 165px;
    height: 165px;
    border: 4px solid var(--ink-light);
    border-radius: 50%;
    display: flex;
    align-items: center;
    justify-content: center;
    text-align: center;
  }
  .brand-name {
    font-family: "Federo", sans-serif;
    font-size: 22px;
    line-height: 1.15;
    color: var(--ink-light);
    font-weight: 400;
    padding: 0 14px;
  }
  .tagline {
    position: absolute;
    left: 842px;
    top: 193px;
    font-family: "Federo", sans-serif;
    font-size: 36px;
    line-height: 39px;
    color: var(--ink-light);
    letter-spacing: 0.5px;
  }
  .elk-illustration {
    position: absolute;
    left: 977px;
    top: 295px;
    width: 141px;
    height: 127px;
    background: linear-gradient(180deg, rgba(255,255,255,0.55), rgba(255,255,255,0.85));
    border-top-left-radius: 40px;
  }
</style>
</head>
<body>
  <section class="backdrop-wall">
    <div class="forest-scene" role="img" aria-label="Painterly redwood forest with tall red-brown trunks, green ferns and a wooden-fenced path"></div>
    <div class="cutout cutout--left"></div>
    <div class="cutout cutout--center"></div>
    <div class="brand-mark">
      <p class="brand-name">Fern Hollow Roastery</p>
    </div>
    <h1 class="tagline">NATURE<br>FRIENDLY<br>COFFEE SHOP</h1>
    <div class="elk-illustration" role="img" aria-label="Distressed white elk head illustration with antlers"></div>
  </section>
</body>
</html>
```